High-End Print/Digital Ad for Unique Luxury Travel Company Required

Objective:
Design a compelling and visually striking advertisement that highlights our company’s unmatched luxury travel experiences. The ad should elevate our brand image, spark curiosity, and drive prospective clients to contact us.
Target Audience:
• Affluent individuals seeking extraordinary, tailor-made travel experiences
• Affluent, luxury, high-net-worth individuals looking for value, expertise, and white-glove service
• Professionals or retirees who appreciate unique, thoughtfully curated travel over mainstream tourism
Key Messages to Communicate:
• One-of-a-kind luxury travel: Once-in-a-lifetime experiences that are curated with creativity and meticulous attention to detail
• Exceptional service: White-glove, personalized planning from start to finish
• 38 years’ travel experience – expert knowledge of destinations, modes of travel, premium accommodations and well-established, meaningful industry connections.
• Highly trusted: Cruise line executives often say, “No one does what you do.”
Tone and Style:
• Elegant, luxurious, sophisticated
• Eye-catching, polished, and modern
• Professional but warm—conveys trust and credibility
• High-impact visuals (full-bleed imagery, custom graphics, or high-end photography)
Deliverables:
• One full-page print ad and digital ad
• Ready-to-print, high-resolution file + working file (PSD, AI, etc.)
Optional: Social media-optimized version or short motion-graphic variation (if designer offers it)
Inspiration & Visual Style Suggestions:
• Think Lumen Voyages, Harrow Pike Wanderer, Silver Quill, or Orvel Retreats ad styles
• Large, emotive imagery with elegant typography
• Clean layout that speaks luxury, clarity, and trust
Copy Direction (draft):
For those who’ve explored the world—and crave something beyond the ordinary.
Each journey is a masterfully curated experience, rich in detail, seamless in execution, and unforgettable in every way.
Founded in 1997, Tidewell Journeys is a unique travel company specializing in cruising, all-inclusive luxury properties, and tours world-wide for individuals, groups, and incentives.
We offer an exceptional range of services designed to ensure every journey is flawlessly executed and truly unforgettable.
Let us help you plan your next extraordinary adventure.
Note: You may refine the copy slightly based on layout or format needs.
Other Resources for References:
1. Website - www.tidewelljourneys-example.com

```html
<!DOCTYPE html>
<html lang="en">
<head>
<meta charset="utf-8">
<title>Tidewell Journeys — Luxury Travel Ad</title>
<link rel="stylesheet" href="https://fonts.googleapis.com/css2?family=Figtree:ital,wght@0,400;0,500;1,400;1,500&family=Libre+Baskerville:wght@400;700&display=swap">
<style>
  :root{
    --navy:#0e4a82;
    --navy-deep:#0b3f72;
    --panel:rgba(8,46,58,0.93);
    --white:#ffffff;
    --travel-blue:rgba(190,225,245,0.85);
  }
  *{margin:0;padding:0;box-sizing:border-box}
  html,body{width:927px;height:1200px;overflow:hidden;background:var(--white)}
  .ad{position:relative;width:927px;height:1200px;overflow:hidden;font-family:"Figtree",sans-serif}
  .hero-photo{position:absolute;left:0;top:0;width:927px;height:1071px;
    background:linear-gradient(180deg,#37c3f0 0%,#7fd6f2 10%,#6cc4e6 20%,#2d8cc4 28%,#1f6ea6 38%,#1d6aa0 44%,#4f8a4a 50%,#6f9a3e 56%,#5f8f3a 62%,#e8eef2 66%,#f2f4f6 71%,#1e9bc2 76%,#1a8fb8 100%)}
  .travel-word{position:absolute;left:30px;top:30px;width:90px;height:440px;overflow:visible}
  .travel-word text{font-family:"Libre Baskerville",serif;font-weight:400;font-size:100px;fill:var(--travel-blue)}
  .side-rule{position:absolute;left:149px;top:25px;width:1px;height:461px;background:var(--white)}
  .headline{position:absolute;left:186px;top:58px;width:710px;height:70px;overflow:visible}
  .headline text{font-family:"Libre Baskerville",serif;font-weight:700;font-size:62px;fill:var(--navy)}
  .intro{position:absolute;left:227px;width:672px;font-style:italic;font-size:18.5px;line-height:29px;color:var(--white)}
  .intro.p1{top:178px}
  .intro.p2{top:282px}
  .intro.p3{top:391px}
  .intro .brand{font-weight:500;text-decoration:underline;text-underline-offset:3px}
  .features{position:absolute;left:37px;top:754px;width:853px;height:314px;background:var(--panel);
    border:1px solid rgba(255,255,255,0.85);border-bottom:none;border-radius:8px 8px 0 0}
  .feature{position:absolute;left:0;width:100%;height:60px}
  .feature .icon{position:absolute;left:60px;top:7px;width:46px;height:46px}
  .feature .title{position:absolute;left:137px;top:17px;font-style:italic;font-size:20px;color:var(--white)}
  .feature .desc{position:absolute;left:440px;top:6px;width:390px;font-style:italic;font-size:14px;line-height:22px;color:var(--white)}
  .f1{top:34px}.f2{top:127px}.f3{top:219px}
  .base-bar{position:absolute;left:30px;top:1066px;width:876px;height:5px;border-radius:3px;background:var(--navy-deep)}
  .footer-brand{position:absolute;left:36px;top:1117px;display:flex;align-items:center;gap:10px}
  .footer-brand .mark{width:30px;height:30px;border-radius:50%;background:var(--navy)}
  .footer-brand .name{font-size:30px;font-weight:500;color:var(--navy);letter-spacing:0.5px}
  .footer-rule{position:absolute;left:417px;top:1095px;width:1px;height:83px;background:var(--navy)}
  .tagline{position:absolute;left:451px;top:1096px;font-style:italic;font-size:18px;color:var(--navy)}
  .contact{position:absolute;top:1138px;display:flex;align-items:center;gap:18px;font-size:15px;color:var(--navy-deep)}
  .contact svg{width:18px;height:18px}
  .contact.phone{left:455px}
  .contact.email{left:636px}
</style>
</head>
<body>
<div class="ad">
  <div class="hero-photo" role="img" aria-label="Aerial photo of a large white cruise ship docked at a green tropical island harbour with hillside villas, blue sea and a bright cloudy sky"></div>

  <svg class="travel-word" viewBox="0 0 90 440" aria-label="Travel">
    <text x="-437" y="82" transform="rotate(-90)" textLength="430" lengthAdjust="spacingAndGlyphs">TRAVEL</text>
  </svg>
  <div class="side-rule"></div>

  <svg class="headline" viewBox="0 0 710 70" role="heading" aria-level="1" aria-label="Tidewell Journeys">
    <text x="0" y="58" textLength="702" lengthAdjust="spacingAndGlyphs">TIDEWELL JOURNEYS</text>
  </svg>

  <p class="intro p1">For those who’ve explored the world—and crave something beyond the ordinary. Each journey is a masterfully curated experience, rich in detail, seamless in execution, and unforgettable in every way.</p>
  <p class="intro p2">Founded in 1997, <span class="brand">Tidewell Journeys</span> is a unique travel company specializing in cruising, all-inclusive luxury properties, and tours world-wide for individuals, groups, and incentives.</p>
  <p class="intro p3">We offer an exceptional range of services designed to ensure every journey is flawlessly executed and truly unforgettable.</p>

  <section class="features">
    <div class="feature f1">
      <svg class="icon" viewBox="0 0 46 46" fill="none" stroke="#fff" stroke-width="1.4">
        <circle cx="23" cy="23" r="20"/><circle cx="23" cy="23" r="14"/>
        <path d="M16 20l3-4h8l3 4-7 9z M16 20h14 M20 20l3 9 3-9"/>
      </svg>
      <div class="title">One-of-a-Kind Luxury Travel</div>
      <div class="desc">Once-in-a-lifetime experiences that are curated with creativity and meticulous attention to detail.</div>
    </div>
    <div class="feature f2">
      <svg class="icon" viewBox="0 0 46 46" fill="none" stroke="#fff" stroke-width="1.4">
        <path d="M20 8l2.5 5 5.5.8-4 3.9 1 5.5-5-2.6-5 2.6 1-5.5-4-3.9 5.5-.8z"/>
        <path d="M5 28h30 M7 31c4 8 14 10 22 6l5-4 M37 33h5v10h-5z"/>
        <path d="M20 2v3 M11 5l2 2 M29 5l-2 2"/>
      </svg>
      <div class="title">Exceptional Trusted Service</div>
      <div class="desc">White-glove, personalized planning from start to finish like no where you have experienced.</div>
    </div>
    <div class="feature f3">
      <svg class="icon" viewBox="0 0 46 46" fill="none" stroke="#fff" stroke-width="1.4">
        <path d="M23 1l3 19 20 3-20 3-3 19-3-19-20-3 20-3z"/>
        <path d="M15 15l8 8 8-8 M15 31l8-8 8 8"/>
      </svg>
      <div class="title">38 Years’ Travel Experience</div>
      <div class="desc">Expert knowledge of destinations, premium and well-established, meaningful industry connections.</div>
    </div>
  </section>
  <div class="base-bar"></div>

  <div class="footer-brand">
    <span class="mark"></span>
    <span class="name">Tidewell Journeys</span>
  </div>
  <div class="footer-rule"></div>
  <p class="tagline">Let us help you plan your next extraordinary adventure.</p>
  <div class="contact phone">
    <svg viewBox="0 0 24 24" fill="none" stroke="#0e4a82" stroke-width="1.8" stroke-linejoin="round"><path d="M5 3h4l2 5-2.5 1.5a11 11 0 0 0 6 6L16 13l5 2v4a2 2 0 0 1-2 2A16 16 0 0 1 3 5a2 2 0 0 1 2-2z"/></svg>
    <span>1-800-555-0142</span>
  </div>
  <div class="contact email">
    <svg viewBox="0 0 24 24" fill="none" stroke="#0e4a82" stroke-width="1.8"><rect x="3" y="5" width="18" height="14" rx="1"/><path d="M3 6l9 7 9-7"/></svg>
    <span>hello@tidewell-example.com</span>
  </div>
</div>
</body>
</html>
```